Business Card

THIS IS THE CARD INFORMATION
DEVELOPMENT I FINANCING I PROPERTY MANAGEMENT
DANIEL OKAFOR
3182 SW 74th Terrace
Palm Hollow, FL 34518
Telephone I 855.437.2618
Facsimile I 855.437.2675
Industry/Entity Type
Business

```html
<!DOCTYPE html>
<html lang="en">
<head>
<meta charset="utf-8">
<title>Brightwell Group — Business Card</title>
<link rel="stylesheet" href="https://fonts.googleapis.com/css2?family=Ubuntu:wght@500;700&family=Open+Sans:wght@400;600&display=swap">
<style>
  :root {
    --page-bg: #e9e7e4;
    --card-bg: #ffffff;
    --ink: #1c1c1e;
    --ink-soft: #4a4a4e;
    --brand-purple: #9b1f8f;
    --band-black: #1f1f21;
  }
  * { margin: 0; padding: 0; box-sizing: border-box; }
  html, body {
    width: 1200px;
    height: 1023px;
    overflow: hidden;
    background: var(--page-bg);
  }
  .stage {
    width: 1200px;
    height: 1023px;
    display: flex;
    align-items: center;
    justify-content: center;
  }
  .business-card {
    position: relative;
    width: 1000px;
    height: 572px;
    background: var(--card-bg);
    border-radius: 34px;
    overflow: hidden;
    box-shadow: 0 10px 30px rgba(0,0,0,0.12);
  }
  .edge-band {
    position: absolute;
    left: 0;
    top: 0;
    width: 90px;
    height: 572px;
  }
  .brand {
    position: absolute;
    left: 150px;
    top: 110px;
    display: flex;
    align-items: center;
    gap: 20px;
  }
  .brand-dot {
    width: 56px;
    height: 56px;
    border-radius: 50%;
    background: var(--brand-purple);
    flex: none;
  }
  .brand-name {
    font-family: "Ubuntu", sans-serif;
    font-weight: 700;
    font-size: 58px;
    line-height: 1;
    color: var(--ink);
    letter-spacing: -0.5px;
  }
  .contact {
    position: absolute;
    left: 150px;
    top: 262px;
    font-family: "Open Sans", sans-serif;
    color: var(--ink-soft);
    font-size: 27px;
    line-height: 1.32;
  }
  .contact-name {
    font-family: "Ubuntu", sans-serif;
    font-weight: 500;
    color: var(--brand-purple);
    font-size: 31px;
    letter-spacing: 0.5px;
    margin-bottom: 6px;
  }
  .contact .label { color: var(--brand-purple); }
  .tagline {
    position: absolute;
    left: 150px;
    bottom: 70px;
    font-family: "Open Sans", sans-serif;
    font-size: 21px;
    letter-spacing: 0.6px;
    color: var(--ink-soft);
  }
  .tagline .sep { color: var(--brand-purple); margin: 0 6px; }
</style>
</head>
<body>
<main class="stage">
  <article class="business-card">
    <svg class="edge-band" viewBox="0 0 90 572" aria-hidden="true">
      <defs>
        <linearGradient id="purpleBand" x1="0" y1="0" x2="1" y2="0">
          <stop offset="0" stop-color="#5e1258"/>
          <stop offset="0.55" stop-color="#9b1f8f"/>
          <stop offset="1" stop-color="#6e1468"/>
        </linearGradient>
      </defs>
      <polygon points="0,0 70,0 70,150 0,190" fill="#1f1f21"/>
      <polygon points="0,330 70,290 90,290 90,572 0,572" fill="url(#purpleBand)"/>
    </svg>

    <header class="brand">
      <span class="brand-dot"></span>
      <h1 class="brand-name">BRIGHTWELL GROUP</h1>
    </header>

    <section class="contact">
      <p class="contact-name">DANIEL OKAFOR</p>
      <p><span class="label">T</span> : 855.437.2618</p>
      <p><span class="label">F</span> : 855.437.2675</p>
      <p>3182 SW 74th Terrace</p>
      <p>Palm Hollow, FL 34518</p>
    </section>

    <p class="tagline">DEVELOPMENT<span class="sep">|</span>FINANCING<span class="sep">|</span>PROPERTY MANAGEMENT</p>
  </article>
</main>
</body>
</html>
```